Book cover design for a collection of poetry - The Lanternfield

Book cover and back design need to be moody, nostalgic, reflective, ethereal. Melancholy and other worldly. Cover design should not be time specific to a period or place but if applicable should reflect British landscape. Book cover should be in tones of blue and must include the title and author (THE LANTERNFIELD BY CORBIN WHITLACE). We love the idea of rain, and looking out of a window. See attached designs. A world you are observing but not in.

Industry/Entity Type

Book Publisher

Font styles to use
Serif
Script

Colors
3176b5
3377b5
85acd3
eaf1f7
0792cd
33a6d7
86cae7
ecf7fb
86cfc6

Requirements
Must have
• The colour blue in it, must be melancholy and reflective.
Nice to have
• Rain in the cover.
Should not have
• Any bright colours.

```html
<!DOCTYPE html>
<html lang="en">
<head>
<meta charset="utf-8">
<title>The Lanternfield — Cover Spread</title>
<link rel="stylesheet" href="https://fonts.googleapis.com/css2?family=EB+Garamond:ital,wght@0,400;0,500;1,400&family=Roboto+Condensed:wght@700&display=swap">
<style>
  :root {
    --paper: #ffffff;
    --trim: #2a2a2a;
    --spine: #0c2027;
    --panel: rgba(8, 20, 48, 0.78);
    --text-light: #eef3f8;
    --title-grey: #cfd0d3;
    --author-frame: #a9dcd8;
    --sky: #3377b5;
    --sky-light: #85acd3;
    --water: #0792cd;
    --foliage: #2f4a3c;
    --foliage-deep: #1a2e2a;
  }
  * { margin: 0; padding: 0; box-sizing: border-box; }
  html, body { width: 1200px; height: 936px; overflow: hidden; background: var(--paper); }
  .spread { position: relative; width: 1200px; height: 936px; }

  .crop-marks { position: absolute; inset: 0; }

  .cover-art {
    position: absolute; top: 39px; height: 854px;
    background:
      radial-gradient(ellipse 40% 30% at 50% 40%, rgba(133,172,211,0.55), transparent 70%),
      linear-gradient(180deg, var(--foliage) 0%, var(--sky) 18%, var(--sky-light) 45%, var(--water) 60%, var(--foliage) 82%, var(--foliage-deep) 100%);
  }
  .cover-art.back { left: 42px; width: 539px; }
  .cover-art.front { left: 622px; width: 539px; }

  .spine {
    position: absolute; left: 581px; top: 39px; width: 41px; height: 854px;
    background: var(--spine);
  }
  .spine-title {
    position: absolute; left: 50%; top: 150px;
    transform: translateX(-50%) rotate(90deg); transform-origin: center;
    white-space: nowrap;
  }
  .spine-text {
    position: absolute; left: 8px; writing-mode: vertical-rl;
    white-space: nowrap;
  }
  .spine-text.title {
    top: 148px;
    font-family: "EB Garamond", serif; font-size: 23px; letter-spacing: 1px;
    color: var(--title-grey);
  }
  .spine-text.author {
    top: 648px; left: 12px;
    font-family: "Roboto Condensed", sans-serif; font-weight: 700; font-size: 14px;
    color: var(--text-light);
  }

  .blurb-panel {
    position: absolute; left: 138px; top: 190px; width: 344px; height: 573px;
    background: var(--panel);
    font-family: "EB Garamond", serif; color: var(--text-light);
    text-align: center; font-size: 15px; line-height: 20px;
    padding: 65px 22px 0;
  }
  .blurb-panel p { margin-bottom: 20px; }
  .blurb-panel .synopsis { margin-bottom: 20px; }
  .blurb-panel .tagline { font-style: italic; margin-bottom: 50px; }
  .blurb-panel .author {
    font-family: "Roboto Condensed", sans-serif; font-weight: 700; font-size: 15px;
    margin-bottom: 25px;
  }
  .blurb-panel .publisher { font-size: 13px; }

  .front-title {
    position: absolute; left: 622px; top: 190px; width: 539px;
    text-align: center; font-family: "EB Garamond", serif; font-weight: 500;
    color: var(--title-grey); text-shadow: 2px 3px 4px rgba(0,0,0,0.45);
    line-height: 1;
  }
  .front-title .line-1 { display: block; font-size: 70px; padding-left: 0; }
  .front-title .line-2 { display: block; font-size: 52px; margin-top: 14px; letter-spacing: 1px; }

  .author-plate {
    position: absolute; left: 796px; top: 757px; width: 196px; height: 39px;
    border: 1.5px solid var(--author-frame);
    display: flex; align-items: center; justify-content: center;
    font-family: "Roboto Condensed", sans-serif; font-weight: 700; font-size: 20px;
    color: var(--text-light);
  }
</style>
</head>
<body>
<div class="spread">
  <svg class="crop-marks" width="1200" height="936" viewBox="0 0 1200 936" aria-hidden="true">
    <g stroke="var(--trim)" stroke-width="0.7">
      <line x1="40" y1="0" x2="40" y2="28"/><line x1="0" y1="39" x2="30" y2="39"/>
      <line x1="1161" y1="0" x2="1161" y2="28"/><line x1="1170" y1="39" x2="1200" y2="39"/>
      <line x1="40" y1="906" x2="40" y2="936"/><line x1="0" y1="894" x2="30" y2="894"/>
      <line x1="1161" y1="906" x2="1161" y2="936"/><line x1="1170" y1="894" x2="1200" y2="894"/>
    </g>
  </svg>

  <div class="cover-art back" role="img" aria-label="Mirrored photograph of woodland reflected in still water, blue sky between bare trees and fallen leaves"></div>
  <div class="cover-art front" role="img" aria-label="Mirrored photograph of woodland reflected in still water, blue sky between bare trees and fallen leaves"></div>

  <div class="spine">
    <span class="spine-text title">THE LANTERNFIELD</span>
    <span class="spine-text author">CORBIN WHITLACE</span>
  </div>

  <div class="blurb-panel">
    <p>The Lanternfield is a collection of Poetry.</p>
    <p class="synopsis">Told in two parts we first meet Charles - aged, crippled and left alone in his inherited Marsh house - reflecting on his life and his marriage to beautiful Alice, who we meet in part two.<br>Alice is suicidal, manically depressed and struggling with life as a wife and mother. She meets, harbours and falls in love with a soldier during WWII and her world is changed forever.</p>
    <p class="tagline">Moving through the 20th Century, this life and the next, The Lanternfield interweaves grief, loss, the afterlife, mental illness and ultimately the true nature of love,</p>
    <p class="author">CORBIN WHITLACE</p>
    <p class="publisher">Publisher Information</p>
  </div>

  <h1 class="front-title">
    <span class="line-1">THE</span>
    <span class="line-2">LANTERNFIELD</span>
  </h1>

  <div class="author-plate">CORBIN WHITLACE</div>
</div>
</body>
</html>
```